Employee Benefits and Insurance Consulting

We are an existing company with over 30 years experience but are changing our name. We would like a simple design with grey tones.

Industry/Entity Type

Insurance

Contact Information for Business Card

Marlow Benefits Consulting
Gerald P Hollins CEO
5172 Brackenridge Road
Alderbrook, TN 37990
gerald@marlowbenefits-example.com
865-412-5593 - O
865-247-3861 - C

```html
<!DOCTYPE html>
<html lang="en">
<head>
<meta charset="utf-8">
<title>Marlow Benefits Consulting – Business Card</title>
<link rel="stylesheet" href="https://fonts.googleapis.com/css2?family=Open+Sans:wght@300;400;600&display=swap">
<style>
  :root {
    --backdrop: #8a7a66;
    --card-white: #fbfbfb;
    --card-fade: #e9e9e9;
    --band-light: #dcdcdc;
    --band-dark: #b3b3b3;
    --band-dark-end: #a6a6a6;
    --logo-grey: #a9a9a9;
    --name-grey: #c4c4c4;
    --contact-white: #ffffff;
  }
  html, body {
    margin: 0;
    padding: 0;
    width: 1200px;
    height: 780px;
    overflow: hidden;
    background: var(--backdrop);
  }
  .canvas {
    width: 1200px;
    height: 780px;
    display: flex;
    align-items: center;
    justify-content: center;
  }
  .business-card {
    position: relative;
    width: 1050px;
    height: 600px;
    background: linear-gradient(180deg, var(--card-white) 0%, var(--card-fade) 52%);
    box-shadow: 0 14px 34px rgba(0,0,0,0.35);
    overflow: hidden;
    font-family: "Open Sans", Arial, sans-serif;
  }
  .brand {
    position: absolute;
    top: 120px;
    left: 0;
    right: 0;
    display: flex;
    align-items: center;
    justify-content: center;
    gap: 26px;
  }
  .brand-mark {
    width: 70px;
    height: 70px;
    flex: none;
  }
  .brand-name {
    color: var(--logo-grey);
    font-weight: 400;
    line-height: 1.15;
    text-transform: uppercase;
  }
  .brand-name .line-main {
    display: block;
    font-size: 54px;
    letter-spacing: 2px;
  }
  .brand-name .line-sub {
    display: block;
    font-size: 24px;
    letter-spacing: 22px;
  }
  .name-band {
    position: absolute;
    top: 318px;
    left: 0;
    right: 0;
    height: 78px;
    background: linear-gradient(90deg, var(--band-light), #e6e6e6 50%, var(--band-light));
    display: flex;
    align-items: center;
    justify-content: center;
  }
  .person {
    margin: 0;
    color: var(--name-grey);
    font-size: 36px;
    font-weight: 400;
    letter-spacing: 0.5px;
  }
  .contact-band {
    position: absolute;
    top: 396px;
    left: 0;
    right: 0;
    bottom: 0;
    background: linear-gradient(90deg, var(--band-dark), var(--band-dark-end));
    display: flex;
    flex-direction: column;
    align-items: center;
    justify-content: center;
    gap: 8px;
    color: var(--contact-white);
    font-size: 29px;
    font-weight: 300;
  }
  .contact-band p { margin: 0; white-space: nowrap; }
  .contact-band .label { font-weight: 600; }
  .phone-pair .gap { display: inline-block; width: 26px; }
</style>
</head>
<body>
  <main class="canvas">
    <article class="business-card">
      <header class="brand">
        <svg class="brand-mark" viewBox="0 0 70 70" aria-hidden="true">
          <circle cx="35" cy="35" r="30" fill="var(--logo-grey)"/>
        </svg>
        <div class="brand-name">
          <span class="line-main">Marlow Benefits</span>
          <span class="line-sub">Consulting</span>
        </div>
      </header>

      <section class="name-band">
        <h1 class="person">Gerald P Hollins | CEO</h1>
      </section>

      <section class="contact-band">
        <p class="phone-pair"><span class="label">O:</span> 865-412-5593<span class="gap"></span><span class="label">C:</span> 865-247-3861</p>
        <p class="email">gerald@marlowbenefits-example.com</p>
        <p class="address">5172 Brackenridge Road Alderbrook, TN 37990</p>
      </section>
    </article>
  </main>
</body>
</html>
```